Modern Business Card

Modern professional business card with more than just logo and demographic info. Something memorable.

We are a trendy/modern chiropractic group with an emphasis on neurology, hence the minimalist-type brain logo. We want to convey that modern and technical aspect with professionalism and the elite nature of our practice environment.

```html
<!DOCTYPE html>
<html lang="en">
<head>
<meta charset="utf-8">
<title>Meridian Spine Care – Business Card</title>
<link href="https://fonts.googleapis.com/css2?family=Arvo:wght@400;700&display=swap" rel="stylesheet">
<style>
  :root {
    --stage: #2a2a2c;
    --card-white: #ffffff;
    --brand-blue: #4a7fc3;
    --brand-blue-light: #6a98d4;
    --brand-blue-deep: #3f6fae;
    --ink: #1b1b1b;
    --rule: #9a9a9a;
    --rule-soft: #d4d4d4;
  }
  html, body {
    margin: 0;
    padding: 0;
    width: 1200px;
    height: 1108px;
    overflow: hidden;
    background: var(--stage);
  }
  .stage {
    width: 1200px;
    height: 1108px;
    display: flex;
    align-items: center;
    justify-content: center;
    gap: 80px;
  }
  .card {
    width: 400px;
    height: 680px;
    border-radius: 26px;
    box-sizing: border-box;
    position: relative;
    overflow: hidden;
    box-shadow: 0 18px 40px rgba(0, 0, 0, 0.45);
  }

  /* Front */
  .card-front {
    background: var(--card-white);
    font-family: "Arvo", serif;
    color: var(--ink);
    text-align: center;
    padding: 128px 40px 0;
  }
  .brand {
    display: flex;
    align-items: center;
    justify-content: center;
    gap: 14px;
  }
  .brand-square {
    width: 24px;
    height: 24px;
    background: var(--brand-blue);
    flex: none;
  }
  .brand-name {
    font-weight: 700;
    font-size: 27px;
    line-height: 1.15;
    color: var(--ink);
    text-transform: uppercase;
    text-align: left;
    letter-spacing: 1px;
  }
  .person { margin-top: 150px; }
  .person-name {
    font-weight: 700;
    font-size: 27px;
    color: var(--brand-blue);
    text-transform: uppercase;
    margin: 0;
  }
  .person-role {
    font-size: 17px;
    margin: 4px 0 0;
  }
  .divider {
    display: flex;
    align-items: center;
    gap: 8px;
    margin: 14px 0 12px;
  }
  .divider::before, .divider::after {
    content: "";
    flex: 1;
    height: 1px;
    background: var(--rule);
  }
  .icon {
    width: 26px;
    height: 26px;
    border-radius: 4px;
    background: var(--brand-blue);
    display: flex;
    align-items: center;
    justify-content: center;
  }
  .contact {
    font-size: 17px;
    line-height: 1.45;
    margin: 0;
  }
  .address {
    border-top: 1px solid var(--rule-soft);
    margin: 12px 0 0;
    padding-top: 12px;
    font-size: 17px;
    line-height: 1.45;
  }

  /* Back */
  .card-back { background: var(--brand-blue); }
  .back-pattern {
    position: absolute;
    inset: 0;
    background:
      radial-gradient(ellipse 70% 45% at 50% 20%, rgba(255,255,255,0.16), rgba(255,255,255,0) 70%),
      radial-gradient(ellipse 80% 45% at 50% 88%, rgba(30,60,110,0.28), rgba(30,60,110,0) 70%),
      linear-gradient(180deg, var(--brand-blue-light) 0%, var(--brand-blue) 50%, var(--brand-blue-deep) 100%);
  }
  .back-brand {
    position: absolute;
    left: 0;
    right: 0;
    top: 400px;
    display: flex;
    align-items: center;
    justify-content: center;
    gap: 12px;
  }
  .back-square {
    width: 20px;
    height: 20px;
    background: var(--card-white);
    flex: none;
  }
  .back-name {
    font-family: "Arvo", serif;
    font-weight: 700;
    font-size: 22px;
    color: var(--card-white);
    text-transform: uppercase;
    letter-spacing: 1px;
  }
</style>
</head>
<body>
<main class="stage">
  <section class="card card-front">
    <div class="brand">
      <span class="brand-square"></span>
      <span class="brand-name">Meridian<br>Spine Care</span>
    </div>
    <div class="person">
      <h1 class="person-name">Daniel Harper</h1>
      <p class="person-role">Managing Director</p>
    </div>
    <div class="divider">
      <span class="icon">
        <svg width="16" height="16" viewBox="0 0 16 16"><path d="M3 2h3l1 3-2 1a8 8 0 0 0 5 5l1-2 3 1v3c0 1-1 1-1 1A12 12 0 0 1 2 3s0-1 1-1z" fill="#fff"/></svg>
      </span>
      <span class="icon">
        <svg width="16" height="16" viewBox="0 0 16 16"><rect x="2" y="4" width="12" height="8" fill="none" stroke="#fff" stroke-width="1.4"/><path d="M2 4l6 5 6-5" fill="none" stroke="#fff" stroke-width="1.4"/></svg>
      </span>
      <span class="icon">
        <svg width="16" height="16" viewBox="0 0 16 16"><circle cx="8" cy="8" r="5.5" fill="none" stroke="#fff" stroke-width="1.4"/><path d="M2.5 8h11M8 2.5c-2 2-2 9 0 11M8 2.5c2 2 2 9 0 11" fill="none" stroke="#fff" stroke-width="1"/></svg>
      </span>
    </div>
    <p class="contact">044-987 654 321<br>hello@mailsample.com<br>www.samplesite.com</p>
    <p class="address">87, Street line here,<br>10234,Country Name</p>
  </section>

  <section class="card card-back">
    <div class="back-pattern" role="img" aria-label="Repeating faint brand symbol pattern in light and deep blue tones"></div>
    <div class="back-brand">
      <span class="back-square"></span>
      <span class="back-name">Meridian Spine Care</span>
    </div>
  </section>
</main>
</body>
</html>
```